Custom Cabinet Shop Needs a website design

Hi,
We need a website for a Custom Cabinet Shop and Cabinet parts manufacturing business.
The business has two sides to it. One side provides custom Kitchens, vanities, entertainment units, offices and what not to homeowners and contractors.
The 2nd side of the business provides built to order cabinet boxes and other parts required to put together a project to other cabinet shops, small contractors looking to install there own cabinets.
Website will need a Gallery to display work.
Color scheme to go well with logo.
current website is www.brambleoakcustomcabinets.com
being changed to www.brambleoak.ca
Logo Included in attached files.
Tagline "Joinery with Spirit"
Mission Statement "Our passion is to deliver inspired cabinetry solutions to suit all your needs, supported by our phenomenal star class customer service"
The website should convey quality and professionalism.
Thank you.
Homeowners/ Contractors
Entertainment

```html
<!DOCTYPE html>
<html lang="en">
<head>
<meta charset="utf-8">
<title>Brambleoak Custom Cabinets</title>
<link href="https://fonts.googleapis.com/css2?family=PT+Sans:ital,wght@0,400;0,700;1,400;1,700&family=Arimo:ital,wght@0,400;0,700;1,400&display=swap" rel="stylesheet">
<style>
:root{
  --orange:#f0531c;
  --orange-bright:#ff5a1f;
  --nav-dark:#2e2e2e;
  --ink:#333333;
  --muted:#777777;
  --card-tint:#e5dcd8;
  --footer:#4a4a4a;
  --footer-base:#333333;
  --white:#ffffff;
}
*{box-sizing:border-box;margin:0;padding:0}
html,body{width:1200px;height:2267px;overflow:hidden;background:var(--white)}
body{position:relative;font-family:"Arimo",Arial,sans-serif;color:var(--ink)}
.abs{position:absolute}

/* header */
.topbar{left:0;top:0;width:1200px;height:44px;background:var(--white)}
.phone{left:830px;top:12px;font-size:17px;color:#444;display:flex;align-items:center;gap:8px}
.social-top{left:970px;top:8px;display:flex;gap:4px}
.social-top span{width:27px;height:27px;border-radius:50%;background:var(--orange);display:block}
.navband{left:0;top:44px;width:1200px;height:59px;background:linear-gradient(#3d3d3d,#262626)}
.brand-box{left:112px;top:0;width:234px;height:113px;background:var(--white);border:1px solid var(--orange);display:flex;align-items:center;justify-content:center;gap:10px;z-index:3}
.brand-box .dot{width:22px;height:22px;border-radius:50%;background:var(--orange)}
.brand-box .name{font-family:"PT Sans",sans-serif;font-weight:700;font-size:27px;color:var(--nav-dark);letter-spacing:.5px}
.tagline{left:363px;top:63px;font-style:italic;font-size:16px;color:#e8e8e8}
.nav{left:650px;top:41px;height:63px;display:flex;align-items:center}
.nav a{color:var(--white);text-decoration:none;font-family:"PT Sans",sans-serif;font-size:15px;height:63px;display:flex;align-items:center;padding:0 17px}
.nav a.active{background:var(--orange);font-weight:700;padding:0 12px;margin-right:10px}

/* hero */
.hero{left:0;top:103px;width:1200px;height:547px;
  background:
    linear-gradient(180deg,rgba(255,255,255,0) 55%,rgba(95,85,80,.55) 100%),
    linear-gradient(90deg,#8a4a2a 0%,#b0b6ba 7%,#7d8084 14%,#a8613a 20%,#d5e0e6 30%,#b9d3dc 45%,#e4ecef 58%,#cfd9dd 70%,#b86a3f 80%,#9a4d28 92%,#7c3a1d 100%)}
.hero-panel{left:308px;top:307px;width:584px;height:166px;background:rgba(35,35,35,.78);text-align:center;color:var(--white)}
.hero-panel h1{font-family:"PT Sans",sans-serif;font-weight:700;font-size:44px;margin-top:17px;letter-spacing:.5px}
.hero-panel p{font-size:16px;line-height:24px;margin-top:10px;color:#eee}
.hero-fold{left:870px;top:451px}

/* feature cards */
.feature{top:709px;width:209px}
.feature .thumb{height:175px;position:relative}
.feature .frame{position:absolute;left:15px;top:13px;right:15px;bottom:13px;border:2px solid var(--orange);display:flex;align-items:center;justify-content:center;text-align:center;color:var(--white);font-family:"PT Sans",sans-serif;font-weight:700;font-size:17px;line-height:22px}
.feature p{text-align:center;font-size:13.5px;line-height:23px;margin-top:16px;color:#333}
.feature .btn{display:block;width:107px;height:33px;margin:12px auto 0;background:var(--orange-bright);color:var(--white);font-family:"PT Sans",sans-serif;font-weight:700;font-size:14px;line-height:33px;text-align:center}
.tone-a{background:linear-gradient(160deg,#6b5a4c 0%,#3a3430 45%,#242120 100%)}
.tone-b{background:linear-gradient(160deg,#8f7a64 0%,#5a4a3d 50%,#2f2824 100%)}
.tone-c{background:linear-gradient(160deg,#9a9890 0%,#6a6a62 45%,#3f3e3a 100%)}
.tone-d{background:linear-gradient(160deg,#55534d 0%,#3b3a35 50%,#26251f 100%)}

/* services */
.services{left:0;top:1093px;width:1200px;height:339px;background:
  linear-gradient(180deg,rgba(30,25,22,.35),rgba(30,25,22,.55)),
  linear-gradient(90deg,#5a4638 0%,#3f342d 25%,#6b5a4a 50%,#4a3f37 75%,#6a5f56 100%)}
.section-title{left:0;width:1200px;text-align:center;font-family:"PT Sans",sans-serif;font-weight:700;font-size:38px;display:flex;justify-content:center;align-items:center;gap:14px}
.section-title i{display:block;width:96px;border-top:2px dotted currentColor;opacity:.7}
.services .section-title{top:34px;color:var(--white)}
.service-img{width:155px;height:129px;border:2px solid var(--orange);padding:7px}
.service-img div{width:100%;height:100%;background:var(--white);position:relative}
.service-img .fill-box{background:linear-gradient(135deg,#ffffff 20%,#e7c9a0 50%,#c8965e 70%,#ffffff 85%)}
.service-img .fill-doors{background:linear-gradient(90deg,#ffffff 10%,#d8c9a8 30%,#b88a4e 45%,#ffffff 58%,#3a2a22 66%,#2a1e18 82%,#ffffff 90%)}
.service h3{font-family:"PT Sans",sans-serif;font-weight:700;font-size:24px;color:var(--white)}
.service p{font-size:13px;line-height:20px;color:#eee;width:290px;margin-top:5px}
.service .more{font-size:14px;font-weight:700;font-style:italic;color:var(--white);text-decoration:underline}

/* clients */
.clients-title{top:1470px;color:var(--muted)}
.client{top:1560px;width:269px;height:356px}
.client .avatar{position:absolute;left:58px;top:0;width:152px;height:152px;border-radius:50%;border:3px solid var(--white)}
.avatar.cool{background:linear-gradient(180deg,#a9c3cf 0%,#7fa0b0 45%,#2e2c2c 75%,#f2f2f2 100%)}
.avatar.grey{background:linear-gradient(180deg,#e0dfdd 0%,#bdbab6 45%,#f4f4f4 80%,#e6e6e6 100%)}
.client p{position:absolute;left:14px;right:14px;top:172px;text-align:center;font-style:italic;font-size:13.5px;line-height:23px;color:#333}
.client .role{position:absolute;left:0;bottom:0;width:269px;height:64px;background:var(--orange);color:var(--white);text-align:center;font-family:"PT Sans",sans-serif;font-size:19px;line-height:21px;padding-top:11px}

/* footer */
.footer{left:0;top:1988px;width:1200px;height:233px;background:var(--footer);color:var(--white)}
.footer h4{font-family:"PT Sans",sans-serif;font-weight:700;font-size:21px;margin-bottom:14px}
.footer li{list-style:none;font-size:16px;line-height:25px}
.foot-brand{left:820px;top:52px;width:256px;height:80px;display:flex;align-items:center;justify-content:center;gap:10px}
.foot-brand .dot{width:22px;height:22px;border-radius:50%;background:var(--orange)}
.foot-brand .name{font-family:"PT Sans",sans-serif;font-weight:700;font-size:30px;color:var(--white)}
.foot-social{left:878px;top:151px;display:flex;gap:10px}
.foot-social span{width:33px;height:31px;background:#888;display:block}
.basebar{left:0;top:2221px;width:1200px;height:46px;background:var(--footer-base);color:var(--white);font-size:14px}
</style>
</head>
<body>

<header>
  <div class="abs topbar"></div>
  <div class="abs phone">
    <svg width="12" height="16" viewBox="0 0 12 16"><path d="M3 1 L5 4 L4 6 Q5 9 7 11 L9 10 L11 13 L9 15 Q2 12 1 3 Z" fill="#444"/></svg>
    132 555 019
  </div>
  <div class="abs social-top" aria-label="Social links"><span></span><span></span><span></span><span></span></div>
  <div class="abs navband"></div>
  <div class="abs brand-box"><span class="dot"></span><span class="name">BRAMBLEOAK</span></div>
  <div class="abs tagline">Joinery with Spirit</div>
  <nav class="abs nav">
    <a class="active">Home</a><a>Gallery</a><a>Services</a><a>Warranty</a><a>Contact us</a>
  </nav>
</header>

<section>
  <div class="abs hero" role="img" aria-label="Photo of a modern kitchen with wood cabinets, steel fridge, blue tile wall and bar stools"></div>
  <div class="abs hero-panel">
    <h1>WELCOME TO BRAMBLEOAK</h1>
    <p>Lorem ipsum dolor sit amet, consectetur adipiscing elit, sed do<br>eiusmod tempor incididunt ut labore et</p>
  </div>
  <svg class="abs hero-fold" width="22" height="22" viewBox="0 0 22 22"><path d="M2 20 L20 2 L2 2 Z" fill="#fff"/></svg>
</section>

<section>
  <div class="abs feature" style="left:110px">
    <div class="thumb tone-a" role="img" aria-label="Photo of cabinet door styles"><div class="frame">SHOP DOOR<br>STYLES</div></div>
    <p>Lorem ipsum dolor sit amet,<br>consectetur adipiscing elit, sed<br>diam nonummy nibh euismod.</p>
    <span class="btn">Read More</span>
  </div>
  <div class="abs feature" style="left:367px">
    <div class="thumb tone-b" role="img" aria-label="Photo of a finished kitchen"><div class="frame">EXPLORE KITCHEN<br>GALLERY</div></div>
    <p>Lorem ipsum dolor sit amet,<br>consectetur adipiscing elit, sed<br>diam nonummy nibh euismod.</p>
    <span class="btn">Read More</span>
  </div>
  <div class="abs feature" style="left:624px">
    <div class="thumb tone-c" role="img" aria-label="Photo of a kitchen design in progress"><div class="frame">START YOUR FREE<br>DESIGN</div></div>
    <p>Lorem ipsum dolor sit amet,<br>consectetur adipiscing elit, sed<br>diam nonummy nibh euismod.</p>
    <span class="btn">Read More</span>
  </div>
  <div class="abs feature" style="left:881px">
    <div class="thumb tone-d" role="img" aria-label="Photo of a dark wood kitchen"><div class="frame">SEE THE<br>SAVINGS</div></div>
    <p>Lorem ipsum dolor sit amet,<br>consectetur adipiscing elit, sed<br>diam nonummy nibh euismod.</p>
    <span class="btn">Read More</span>
  </div>
</section>

<section class="abs services" role="img" aria-label="Background photo of a warm living room interior">
  <h2 class="abs section-title"><i></i>Our Services<i></i></h2>
  <div class="abs service" style="left:112px;top:138px">
    <div class="service-img"><div class="fill-box" role="img" aria-label="Picture of an open cabinet box"></div></div>
  </div>
  <div class="abs service" style="left:287px;top:132px">
    <h3>Residential</h3>
    <p>Here at Brambleoak Custom Cabinets we are proud to be involved in the custom cabinet market. By employing and partnering up with local artisans we are able to deliver a product that is second to none.</p>
  </div>
  <span class="abs service" style="left:506px;top:270px"><span class="more">Read More</span></span>
  <div class="abs service" style="left:632px;top:138px">
    <div class="service-img"><div class="fill-doors" role="img" aria-label="Picture of cabinet door samples"></div></div>
  </div>
  <div class="abs service" style="left:805px;top:132px">
    <h3>Business</h3>
    <p>At Brambleoak Custom Cabinets we understand that contractors, renovators, home builders, design firms and designers are the foundation of any cabinet shop. We believe that if we work with you to help your.</p>
  </div>
  <span class="abs service" style="left:1020px;top:270px"><span class="more">Read More</span></span>
</section>

<section>
  <h2 class="abs section-title clients-title"><i></i>Our Clients<i></i></h2>
  <div class="abs client" style="left:110px">
    <svg class="abs" style="left:0;top:60px" width="269" height="296"><polygon points="0,42 70,0 199,0 269,42 269,296 0,296" fill="var(--card-tint)"/></svg>
    <div class="avatar cool" role="img" aria-label="Client portrait"></div>
    <p>Lorem ipsum dolor sit amet, consectetur adipiscing elit, sed diam nonummy nibh euismod tincidunt ut laoreet dolore magna aliquam erat eiusmod tempor incididunt ut labore</p>
    <div class="role">Jhon Doe<br>Postions</div>
  </div>
  <div class="abs client" style="left:466px">
    <svg class="abs" style="left:0;top:60px" width="269" height="296"><polygon points="0,42 70,0 199,0 269,42 269,296 0,296" fill="var(--card-tint)"/></svg>
    <div class="avatar grey" role="img" aria-label="Client portrait"></div>
    <p>Lorem ipsum dolor sit amet, consectetur adipiscing elit, sed diam nonummy nibh euismod tincidunt ut laoreet dolore magna aliquam erat eiusmod tempor incididunt ut labore</p>
    <div class="role">Jhon Doe<br>Postions</div>
  </div>
  <div class="abs client" style="left:822px">
    <svg class="abs" style="left:0;top:60px" width="269" height="296"><polygon points="0,42 70,0 199,0 269,42 269,296 0,296" fill="var(--card-tint)"/></svg>
    <div class="avatar cool" role="img" aria-label="Client portrait"></div>
    <p>Lorem ipsum dolor sit amet, consectetur adipiscing elit, sed diam nonummy nibh euismod tincidunt ut laoreet dolore magna aliquam erat eiusmod tempor incididunt ut labore</p>
    <div class="role">Jhon Doe<br>Postions</div>
  </div>
</section>

<footer>
  <div class="abs footer">
    <div class="abs" style="left:110px;top:38px">
      <h4>Sitemap</h4>
      <ul><li>Home</li><li>Gallery</li><li>Services</li><li>Warranty</li><li>Contact us</li></ul>
    </div>
    <div class="abs" style="left:290px;top:38px">
      <h4>Services</h4>
      <ul><li>Residential</li><li>Office</li></ul>
    </div>
    <div class="abs" style="left:493px;top:38px">
      <h4>Contact Info</h4>
      <ul><li>Address : 48 Alder Lane,Us 15010</li><li>Phone : 812.555 0147</li><li>Email : info@brambleoak.ca</li></ul>
    </div>
    <div class="abs foot-brand"><span class="dot"></span><span class="name">BRAMBLEOAK</span></div>
    <div class="abs foot-social" aria-label="Social links"><span></span><span></span><span></span><span></span></div>
  </div>
  <div class="abs basebar">
    <span class="abs" style="left:110px;top:14px">© 2015 BrambleoakCustomCabinets.All Right Reserved</span>
    <span class="abs" style="left:854px;top:14px">Privacy Policy</span>
    <span class="abs" style="left:954px;top:10px;width:1px;height:24px;background:#fff"></span>
    <span class="abs" style="left:967px;top:14px">Terms &amp; Conditions</span>
  </div>
</footer>

</body>
</html>
```